Business Card for brovaLINK

Create a Business Card with an existing logo for brovaLINK AG. We are a Information Technology company that does consulting and developing SW to automate business processes. The main colors are given from the logo.

Industry/Entity Type

Business

Requirements
Nice to have
• we use a a font style Century Gothic in our documents

```html
<!DOCTYPE html>
<html lang="en">
<head>
<meta charset="utf-8">
<title>brovaLINK AG – Business Card</title>
<link href="https://fonts.googleapis.com/css2?family=Didact+Gothic&family=Cinzel:wght@600&display=swap" rel="stylesheet">
<style>
  :root {
    --stage: #000000;
    --paper: #ffffff;
    --ink: #3a3a3a;
    --ink-soft: #2b2b2b;
    --green: #4eaa2f;
    --blue: #2a6fc0;
    --tone-blue: #cfe3f4;
    --tone-green: #dcefc9;
  }
  * { margin: 0; padding: 0; box-sizing: border-box; }
  html, body {
    width: 1200px; height: 1200px; overflow: hidden;
    background: var(--stage);
  }
  .canvas { position: relative; width: 1200px; height: 1200px; }
  .card {
    position: absolute; background: var(--paper); overflow: hidden;
  }
  .card--front { left: 168px; top: 538px; width: 499px; height: 277px; }
  .card--back  { left: 679px; top: 318px; width: 278px; height: 497px; }

  .brand {
    position: absolute; display: flex; align-items: center;
    font-family: "Didact Gothic", "Century Gothic", sans-serif;
    color: var(--ink); white-space: nowrap;
  }
  .brand__dot { border-radius: 50%; background: var(--green); flex: none; }
  .card--front .brand { left: 72px; top: 110px; font-size: 29px; gap: 18px; }
  .card--front .brand__dot { width: 62px; height: 62px; }
  .card--back .brand { left: 44px; top: 88px; font-size: 26px; gap: 12px; }
  .card--back .brand__dot { width: 46px; height: 46px; }

  .decor-area--front {
    position: absolute; left: 357px; top: 0; width: 142px; height: 277px;
    background: linear-gradient(160deg, var(--tone-green) 0%, var(--paper) 40%, var(--tone-blue) 100%);
  }
  .decor-area--back {
    position: absolute; left: 0; top: 225px; width: 120px; height: 255px;
    background: linear-gradient(160deg, rgba(220,239,201,0.5), rgba(255,255,255,0));
  }

  .contact {
    position: absolute; left: 41px; top: 296px;
    font-family: "Didact Gothic", "Century Gothic", sans-serif;
    font-size: 10.5px; letter-spacing: 1.6px; color: var(--ink-soft);
  }
  .contact__name {
    font-family: "Cinzel", "Trajan Pro", serif; font-weight: 600;
    font-size: 11px; letter-spacing: 2px; line-height: 14px; color: #1e1e1e;
  }
  .contact__role {
    font-family: "Cinzel", "Trajan Pro", serif; font-weight: 600; color: var(--green);
    font-size: 10px; letter-spacing: 2px; line-height: 14px;
  }
  .contact__address { margin-top: 13px; line-height: 14px; }
  .contact__list { list-style: none; margin-top: 12px; }
  .contact__list li { display: flex; align-items: center; height: 16.5px; }
  .contact__list svg { width: 10px; height: 10px; margin-right: 15px; flex: none; }

  .band {
    position: absolute; left: 0; bottom: 0; width: 100%; height: 16px;
    background: var(--green);
  }
</style>
</head>
<body>
<main class="canvas">
  <section class="card card--front" aria-label="Card front">
    <div class="decor-area--front" role="img" aria-label="Large decorative brand graphic"></div>
    <div class="brand"><span class="brand__dot"></span><span>brovaLINK</span></div>
  </section>

  <section class="card card--back" aria-label="Card back">
    <div class="decor-area--back" role="img" aria-label="Faint decorative brand graphic"></div>
    <div class="brand"><span class="brand__dot"></span><span>brovaLINK</span></div>
    <div class="contact">
      <p class="contact__name">Lukas Brenner</p>
      <p class="contact__role">CEO</p>
      <p class="contact__address">Lindenstrasse 8, 5400 Baden<br>Switzerland</p>
      <ul class="contact__list">
        <li><svg viewBox="0 0 10 10"><path d="M1 4 Q5 0 9 4 L8 5 L6.5 4 L6.5 3 Q5 2.5 3.5 3 L3.5 4 L2 5 Z M2.5 6 H7.5 L8 9 H2 Z" fill="var(--blue)"/></svg>+41 56 000 12 34</li>
        <li><svg viewBox="0 0 10 10"><rect x="2.5" y="0.5" width="5" height="9" rx="1" fill="none" stroke="var(--blue)"/><line x1="4" y1="8" x2="6" y2="8" stroke="var(--blue)"/></svg>+41 79 000 45 67</li>
        <li><svg viewBox="0 0 10 10"><rect x="0.5" y="2" width="9" height="6" fill="none" stroke="var(--blue)"/><path d="M0.5 2 L5 5.5 L9.5 2" fill="none" stroke="var(--blue)"/></svg>lukas.brenner@brovalink.ch</li>
        <li><svg viewBox="0 0 10 10"><circle cx="5" cy="5" r="4.3" fill="none" stroke="var(--blue)"/><ellipse cx="5" cy="5" rx="2" ry="4.3" fill="none" stroke="var(--blue)"/><line x1="0.7" y1="5" x2="9.3" y2="5" stroke="var(--blue)"/></svg>www.brovalink.ch</li>
      </ul>
    </div>
    <div class="band"></div>
  </section>
</main>
</body>
</html>
```